Retail Sign for Houseplant Campaign

Sign will measure 3 to 4 foot tall by 22.2inches and place on rolling racks of houseplants for a retail promotion in The Birchwell Yard. The theme of the promotion will be "New Year, New You!" Selling points which should be on the sign are Houseplants give you a taste of nature, Houseplants boost air quality inside your home, Indoor plants reduce anxiety, Indoor plants make you more productive, Houseplants improve your concentration and memory.
Updates

Target Market(s)

People who love plants

Industry/Entity Type

Horticulture/ retail

Colors
00AB8E
00BBA5
67D7C9
C6EFE9
E9F9F6
59FF00
82FF00
B8FF75
E3FFCB
F4FFEA
FFF300
FFF600
FEFA6F
FFFEC7
FFFEE8

Requirements
Must have
• Must feel energetic and encourage people to buy plants. Should include 1-2 photos and the selling points listed

```html
<!DOCTYPE html>
<html lang="en">
<head>
<meta charset="utf-8">
<title>New Year, New You! – Benefits of Houseplants</title>
<link href="https://fonts.googleapis.com/css2?family=Kaushan+Script&family=Itim&display=swap" rel="stylesheet">
<style>
  :root {
    --teal: #5fd6c4;
    --teal-deep: #2fa48f;
    --yellow: #f5e85e;
    --lilac: #d9b3f0;
    --pink: #f4909a;
    --pink-shade: rgba(196, 84, 104, 0.16);
    --ink-light: #f6f2fb;
    --stage: #e4e4e4;
  }
  * { margin: 0; padding: 0; box-sizing: border-box; }
  html, body { width: 840px; height: 1200px; overflow: hidden; }
  body { background: var(--stage); position: relative; }

  .sign {
    position: absolute;
    left: 151px; top: 20px;
    width: 537px; height: 1160px;
    overflow: hidden;
    background: var(--teal);
  }
  .sign-shapes { position: absolute; inset: 0; width: 100%; height: 100%; }

  .headline {
    position: absolute;
    font-family: "Kaushan Script", cursive;
    color: #fff;
    font-size: 80px;
    line-height: 1;
    text-shadow: 3px 4px 0 var(--teal-deep);
    white-space: nowrap;
  }
  .headline--first { left: 60px; top: 62px; }
  .headline--second { left: 98px; top: 152px; }

  .benefits-kicker {
    position: absolute; left: 135px; top: 748px;
    font-family: "Itim", sans-serif;
    font-style: italic;
    font-size: 34px;
    color: var(--ink-light);
    text-shadow: 2px 2px 0 rgba(170, 60, 80, 0.35);
  }
  .benefits-title {
    position: absolute; left: 72px; top: 780px;
    font-family: "Itim", sans-serif;
    font-size: 70px;
    line-height: 1;
    color: var(--ink-light);
    text-shadow: 3px 3px 0 rgba(170, 60, 80, 0.35);
    letter-spacing: 1px;
  }
  .benefits-rule {
    position: absolute; left: 73px; top: 855px;
    width: 391px; height: 3px;
    background: var(--ink-light);
    border-radius: 2px;
  }
  .benefits-list {
    position: absolute; left: 73px; top: 876px;
    list-style: none;
    font-family: "Itim", sans-serif;
    font-size: 22px;
    line-height: 31px;
    color: var(--ink-light);
  }
  .benefits-list li {
    position: relative;
    padding-left: 33px;
    margin-bottom: 6px;
  }
  .benefits-list .tick {
    position: absolute; left: 0; top: 4px;
    width: 21px; height: 21px;
  }
</style>
</head>
<body>
  <main class="sign">
    <svg class="sign-shapes" viewBox="0 0 737 1593" preserveAspectRatio="none" aria-hidden="false">
      <defs>
        <linearGradient id="photoTone" x1="0" y1="0" x2="1" y2="1">
          <stop offset="0" stop-color="#eef2f1"/>
          <stop offset="0.55" stop-color="#e7e3dd"/>
          <stop offset="1" stop-color="#d9bfa8"/>
        </linearGradient>
      </defs>

      <g role="img" aria-label="Photo of a smiling woman placing a potted croton plant in a woven basket on a white shelf">
        <rect x="0" y="360" width="737" height="720" fill="url(#photoTone)"/>
      </g>

      <!-- top bands -->
      <path d="M0,0 H737 V440 C650,482 560,508 480,505 C380,500 300,450 250,455 C150,460 60,490 0,525 Z" fill="var(--lilac)"/>
      <path d="M0,0 H737 V428 C650,470 560,496 480,493 C380,488 300,438 250,443 C150,448 60,478 0,513 Z" fill="#ffffff"/>
      <path d="M0,0 H737 V420 C650,462 560,488 480,485 C380,480 300,430 250,435 C150,440 60,470 0,505 Z" fill="var(--yellow)"/>
      <path d="M0,0 H737 V368 C640,430 560,442 480,432 C380,420 320,378 250,378 C150,378 60,440 0,490 Z" fill="var(--teal)"/>

      <!-- bottom bands -->
      <path d="M0,1030 C60,960 150,905 250,905 C330,905 400,955 480,958 C580,962 660,940 737,895 V1593 H0 Z" fill="var(--teal)"/>
      <path d="M0,1048 C60,978 150,948 250,948 C330,948 400,985 480,988 C580,992 660,960 737,910 V1593 H0 Z" fill="#ffffff"/>
      <path d="M0,1054 C60,984 150,955 250,955 C330,955 400,992 480,995 C580,999 660,966 737,916 V1593 H0 Z" fill="var(--yellow)"/>
      <path d="M0,1072 C60,1002 150,975 250,975 C330,975 400,1028 480,1030 C580,1032 660,1000 737,935 V1593 H0 Z" fill="var(--pink)"/>

      <!-- soft circles -->
      <circle cx="600" cy="1520" r="300" fill="var(--pink-shade)"/>
      <circle cx="180" cy="1590" r="210" fill="var(--pink-shade)"/>
    </svg>

    <h1 class="headline-group">
      <span class="headline headline--first">New Year,</span>
      <span class="headline headline--second">New You!</span>
    </h1>

    <p class="benefits-kicker">benefits of</p>
    <h2 class="benefits-title">Houseplants</h2>
    <div class="benefits-rule"></div>

    <ul class="benefits-list">
      <li><svg class="tick" viewBox="0 0 22 22"><circle cx="11" cy="11" r="9.5" fill="none" stroke="#f6f2fb" stroke-width="1.6"/><path d="M6.5,11.3 L9.8,14.4 L15.6,8" fill="none" stroke="#f6f2fb" stroke-width="1.6" stroke-linecap="round" stroke-linejoin="round"/></svg>Give you a taste of nature,</li>
      <li><svg class="tick" viewBox="0 0 22 22"><circle cx="11" cy="11" r="9.5" fill="none" stroke="#f6f2fb" stroke-width="1.6"/><path d="M6.5,11.3 L9.8,14.4 L15.6,8" fill="none" stroke="#f6f2fb" stroke-width="1.6" stroke-linecap="round" stroke-linejoin="round"/></svg>Boost air quality inside your home,</li>
      <li><svg class="tick" viewBox="0 0 22 22"><circle cx="11" cy="11" r="9.5" fill="none" stroke="#f6f2fb" stroke-width="1.6"/><path d="M6.5,11.3 L9.8,14.4 L15.6,8" fill="none" stroke="#f6f2fb" stroke-width="1.6" stroke-linecap="round" stroke-linejoin="round"/></svg>Indoor plants reduce anxiety,</li>
      <li><svg class="tick" viewBox="0 0 22 22"><circle cx="11" cy="11" r="9.5" fill="none" stroke="#f6f2fb" stroke-width="1.6"/><path d="M6.5,11.3 L9.8,14.4 L15.6,8" fill="none" stroke="#f6f2fb" stroke-width="1.6" stroke-linecap="round" stroke-linejoin="round"/></svg>Indoor plants<br>make you more productive,</li>
      <li><svg class="tick" viewBox="0 0 22 22"><circle cx="11" cy="11" r="9.5" fill="none" stroke="#f6f2fb" stroke-width="1.6"/><path d="M6.5,11.3 L9.8,14.4 L15.6,8" fill="none" stroke="#f6f2fb" stroke-width="1.6" stroke-linecap="round" stroke-linejoin="round"/></svg>Improve your<br>concentration and memory.</li>
    </ul>
  </main>
</body>
</html>
```